Ridgeline Lift Works Brochure

I am looking for a multi page brochure that outlines what we do, our services, and our equipment.
We are committed to delivering equipment, operators, and technicians that provide safe, experienced, and reliable access at heights, industrial sites, power lines/facilities, construction, refineries, and other similar type industries across North America.
Our truck mounted aerial lift platforms are the preferred method of servicing at height structures and industrial plants due to their quick setup, unmatched safety, and ability to operate in adverse conditions.
Incorporate the attached images into the brochure. The overall layout should be a couple pages about us, including our commitment to safe work practices, then about the units themselves.
You can get more information from our website www.ridgelineliftpro.example
Our tagline is Safety. Quality. Service.
Colouring for the brochure should complement our red logo. Our logo could also be used as white.

```html
<!DOCTYPE html>
<html lang="en">
<head>
<meta charset="UTF-8">
<title>Ridgeline Lift Works Brochure – Pages 4–5</title>
<link href="https://fonts.googleapis.com/css2?family=Roboto+Slab:wght@700&family=Inter:wght@400;500;700&display=swap" rel="stylesheet">
<style>
  :root{
    --red:#e8212a;
    --ink:#1a1a1a;
    --paper:#ffffff;
    --stage:#000000;
  }
  *{margin:0;padding:0;box-sizing:border-box}
  html,body{width:1200px;height:1200px;overflow:hidden;background:var(--stage)}
  body{position:relative;font-family:"Inter",sans-serif;color:var(--ink)}
  .page{position:absolute;top:180px;width:556px;height:786px;overflow:hidden}
  .page--left{left:37px;background:var(--paper)}
  .page--right{left:602px}
  .heading{position:absolute;left:46px;font-family:"Roboto Slab",serif;font-weight:700;color:var(--red);font-size:32px;line-height:1}
  .heading--vision{top:52px}
  .heading--profile{top:402px}
  .body-text{position:absolute;left:46px;font-size:11.8px;line-height:16.8px;text-align:justify;letter-spacing:.1px}
  .body-text p{margin:0}
  .indent{text-indent:54px}
  .vision-text{top:100px;width:464px}
  .profile-text{top:458px;width:197px}
  .feature{position:absolute;display:flex;align-items:center;gap:8px}
  .feature svg{flex:none}
  .feature__label{font-weight:700;font-size:12.4px;line-height:13px}
  .profile-photo{position:absolute;left:259px;top:479px;width:250px;height:238px;display:flex}
  .profile-photo span{flex:1}
  .profile-photo .p1{background:linear-gradient(180deg,#2a6ccc,#6d9bd6 70%,#8e8f8f)}
  .profile-photo .p2{background:linear-gradient(90deg,#e6ebf0,#c8ccd0 55%,#6a6e72)}
  .profile-photo .p3{background:linear-gradient(180deg,#7fc3ee,#b9dcf2 60%,#8a8b86)}
  .page-tab{position:absolute;top:748px;height:21px;width:40px;background:var(--red);color:#fff;font-weight:700;font-size:10px;display:flex;align-items:center;justify-content:center}
  .page--left .page-tab{left:0;border-radius:0 3px 3px 0}
  .page--right .page-tab{right:0;border-radius:3px 0 0 3px}
  .site-photo{position:absolute;inset:0;background:
    linear-gradient(180deg,rgba(0,0,0,0) 75%,#b7b9bc 88%,#d9d7d2 100%),
    linear-gradient(90deg,#2c2e33 0%,#34363b 30%,#9ea2a8 45%,#2b2c30 58%,#3a3c41 72%,#c7d8ea 82%,#e6eef6 100%)}
  .section-label{position:absolute;left:0;top:46px;width:188px;height:29px;background:var(--red);color:#fff;font-weight:500;font-size:12.4px;display:flex;align-items:center;justify-content:flex-end;padding-right:8px}
</style>
</head>
<body>

<section class="page page--left">
  <h1 class="heading heading--vision">Our Vision</h1>
  <div class="body-text vision-text">
    <p>We are committed to providing unparalleled service and access to the renewables and wind industries. Our equipment is top-of-line in safety and reliability ensuring that our customers receive the best in-class service.</p>
    <p class="indent">Our operators and technicians are provided premier training to ensure they are able to perform safely in any situation. Customer satisfaction is paramount in our values and we are committed to the success of your project however large or small.</p>
  </div>

  <div class="feature" style="left:46px;top:245px">
    <svg width="46" height="46" viewBox="0 0 46 46" fill="none" stroke="var(--red)" stroke-width="2">
      <circle cx="23" cy="23" r="15"/><circle cx="23" cy="23" r="11"/>
      <path d="M17 22h4v8h-4zM21 22l3-6c2 0 2 2 1 5h5c1 0 2 1 1 3l-2 5h-8"/>
      <path d="M23 2v4M23 40v4M2 23h4M40 23h4M8 8l3 3M35 35l3 3M38 8l-3 3M8 38l3-3"/>
    </svg>
    <span class="feature__label">Unparalleled<br>Service</span>
  </div>

  <div class="feature" style="left:227px;top:248px">
    <svg width="40" height="42" viewBox="0 0 40 42" fill="none" stroke="var(--red)" stroke-width="3">
      <path d="M20 3 4 9v12c0 10 7 16 16 19 9-3 16-9 16-19V9z"/>
      <path d="M13 21l5 5 9-10"/>
    </svg>
    <span class="feature__label">Equipments are<br>top-of-line in safety<br>and reliability</span>
  </div>

  <div class="feature" style="left:416px;top:245px">
    <svg width="54" height="58" viewBox="0 0 54 58" fill="none" stroke="var(--red)" stroke-width="2.4">
      <path d="M30 54H3V7h38v20"/><path d="M16 7V3h12v4"/>
      <path d="M8 17l3 3 5-5M8 28l3 3 5-5M8 39l3 3 5-5M8 50l3 3 5-5M20 18h14M20 29h10M20 40h8M20 50h6"/>
      <circle cx="40" cy="40" r="6" fill="var(--red)"/>
      <path d="M40 29v5M40 46v5M29 40h5M46 40h5M32 32l3 3M45 45l3 3M48 32l-3 3M32 48l3-3" stroke-width="3.5"/>
    </svg>
  </div>
  <div class="feature" style="left:414px;top:312px">
    <span class="feature__label">Committed to<br>the success of<br>your project</span>
  </div>

  <div class="feature" style="left:46px;top:320px">
    <svg width="44" height="44" viewBox="0 0 44 44" fill="none" stroke="var(--red)" stroke-width="3">
      <path d="M40 12A20 20 0 1 0 40 32"/>
      <circle cx="9" cy="22" r="5"/><path d="M14 22h20M28 22v5M33 22v5"/>
    </svg>
    <span class="feature__label">Access to the<br>renewables and<br>wind industries</span>
  </div>

  <div class="feature" style="left:227px;top:321px">
    <svg width="40" height="40" viewBox="0 0 40 40" fill="none" stroke="var(--red)" stroke-width="1.6">
      <circle cx="6" cy="4" r="3"/><path d="M3 9h6v12H3zM5 21v8M7 21v8"/>
      <rect x="14" y="1" width="24" height="17"/><circle cx="26" cy="10" r="3.5"/>
      <path d="M26 18v4"/>
      <circle cx="7" cy="31" r="2.5"/><circle cx="20" cy="31" r="2.5"/><circle cx="33" cy="31" r="2.5"/>
      <path d="M2 39c0-4 10-4 10 0M15 39c0-4 10-4 10 0M28 39c0-4 10-4 10 0"/>
    </svg>
    <span class="feature__label">Trained Operators<br>and Technicians</span>
  </div>

  <h2 class="heading heading--profile">Company Profile</h2>
  <div class="body-text profile-text">
    <p>We are a specialized company dedicated to the success of the renewables industry.</p>
    <p class="indent">With <strong>over 65+ years</strong> of combined experience in equipment operation and project managment, we are uniquely positioned to ensure the success of your projects. We specialize in blade access but have also worked, and are certified to provide services in oil and gas and refineries. We are able to provide the most stable access to wind turbine blades, flare stacks, utility lines, high rises and many other complex project scopes required in industry.</p>
  </div>

  <div class="profile-photo" role="img" aria-label="Three photos of truck-mounted aerial lifts extended beside a utility pole, a high-rise building and a refinery flare stack">
    <span class="p1"></span><span class="p2"></span><span class="p3"></span>
  </div>

  <div class="page-tab">4</div>
</section>

<section class="page page--right">
  <div class="site-photo" role="img" aria-label="Photo of aerial lifts and a crane working on a tall steel column inside a large industrial building, with trucks parked in front"></div>
  <div class="section-label">Industrial Construction</div>
  <div class="page-tab">5</div>
</section>

</body>
</html>
```